Attractive Flyer for Moving Company

Our Company is called "Steadfast Haulers".
We provide moving service for home and businesses
We need a flyer for a moving company, located in South Florida USA
Flyer size will be 7 x 5 inches, double sided.

Flyer needs to be very attractive and catchy for eye. I want people to keep it even if they don't need our service. I attached a lot of text in separate word file.
Logo, brief and additional pictures are attached.

```html
<!DOCTYPE html>
<html lang="en">
<head>
<meta charset="utf-8">
<title>Steadfast Haulers – Moving Flyer</title>
<link href="https://fonts.googleapis.com/css2?family=Oswald:wght@400;500;600;700&family=Source+Sans+3:ital,wght@0,400;0,600;0,700;1,600&display=swap" rel="stylesheet">
<style>
  :root{
    --red:#ec1c24;
    --dark:#3a3a3c;
    --ink:#1b1b1b;
    --yellow:#ffd21f;
    --paper:#ffffff;
    --backdrop:#e9e6e2;
    --grey-text:#555;
  }
  *{box-sizing:border-box;margin:0;padding:0}
  html,body{width:1200px;height:868px;overflow:hidden;background:var(--backdrop)}
  body{position:relative;font-family:"Source Sans 3",Arial,sans-serif;color:var(--ink)}
  .flyer{position:absolute;top:35px;width:570px;height:798px;background:var(--paper);overflow:hidden;box-shadow:0 4px 14px rgba(0,0,0,.15)}
  .flyer--front{left:20px}
  .flyer--back{left:610px}
  .layer{position:absolute;left:0;top:0}
  .abs{position:absolute}
  .heading{font-family:"Oswald",Arial,sans-serif;font-weight:700;text-transform:uppercase;line-height:1}

  /* ---------- front ---------- */
  .included-title{left:45px;top:45px;font-size:28px;color:var(--red);font-weight:600}
  .included-list{left:45px;top:86px;width:240px;list-style:none;font-size:16.5px;line-height:21px;color:#2a2a2a}
  .included-list li{position:relative;padding-left:21px;margin-bottom:11px}
  .included-list li::before{content:"";position:absolute;left:0;top:6px;width:11px;height:11px;border-radius:50%;background:var(--red)}
  .brand{display:flex;align-items:center;gap:7px;white-space:nowrap}
  .brand__dot{width:16px;height:16px;border-radius:50%;background:var(--red);flex:none}
  .brand__name{font-family:"Oswald",Arial,sans-serif;font-weight:700;font-size:24px;text-transform:uppercase;color:var(--red);line-height:1;white-space:nowrap}
  .brand--front{right:28px;top:70px}
  .badge__text{left:329px;top:160px;width:152px;text-align:center;font-family:"Oswald",Arial,sans-serif;font-weight:700;font-size:21px;line-height:21px;color:var(--ink)}
  .save{left:395px;top:280px;width:170px;text-align:center;color:#fff;font-size:41px;line-height:47px;font-weight:700}
  .price{top:268px;width:146px;height:156px;background:var(--red);color:#fff;text-align:center;border-radius:4px;padding-top:10px}
  .price::after{content:"";position:absolute;inset:3px;border:1.5px dashed rgba(255,255,255,.75);border-radius:3px}
  .price--two{left:41px}
  .price--three{left:200px}
  .price__amount{font-family:"Oswald",Arial,sans-serif;font-weight:600;font-size:38px;line-height:44px}
  .price__desc{font-size:16px;line-height:19px;font-weight:600}
  .price__crew{font-family:"Oswald",Arial,sans-serif;font-weight:600;font-size:19px;margin-top:4px;white-space:nowrap}
  .deal{left:43px;top:441px;width:304px;height:60px;border-radius:30px;background:var(--dark);color:#fff;text-align:center;padding-top:6px}
  .deal__title{font-family:"Oswald",Arial,sans-serif;font-weight:600;font-size:29px;line-height:32px;text-transform:uppercase}
  .deal__note{font-size:10.5px;font-style:italic;font-weight:600;white-space:nowrap}
  .tollfree{left:50px;top:510px;font-size:28px;font-weight:600;color:var(--dark);white-space:nowrap}
  .voucher-note{right:28px;top:764px;font-size:15px;color:#222;white-space:nowrap}

  /* ---------- back ---------- */
  .headline{right:28px;top:24px;font-size:72px;color:#000;letter-spacing:0;font-weight:700;white-space:nowrap}
  .sub-note{right:28px;top:108px;width:320px;text-align:right;font-size:12.5px;line-height:15px;color:var(--grey-text)}
  .panel{background:var(--red);border-radius:18px}
  .panel--services{left:219px;right:0;top:152px;height:278px}
  .panel-divider{left:372px;right:0;top:429px;height:8px;background:var(--dark)}
  .panel--why{left:219px;right:0;top:448px;height:245px}
  .services-title{right:28px;top:166px;text-align:right;color:#fff;font-size:33px;line-height:35px;font-weight:600}
  .list{right:28px;list-style:none;text-align:right;color:#fff}
  .list li{display:flex;justify-content:flex-end;align-items:flex-start;gap:4px}
  .services-list{top:247px;width:175px;font-family:"Oswald",Arial,sans-serif;font-weight:500;font-size:15px;line-height:18px;text-transform:uppercase}
  .services-list li{margin-bottom:5px}
  .why-title{right:28px;top:464px;color:#fff;font-size:19px;font-weight:700}
  .why-list{top:494px;width:180px;font-size:14px;line-height:17px}
  .why-list li{margin-bottom:4px}
  .why-list small{display:block;font-size:9px;line-height:10px}
  .tick{flex:none;width:12px;height:12px;margin-top:3px}
  .licensed{left:33px;top:727px;width:245px;height:33px;border-radius:17px;background:var(--dark);color:#fff;text-align:center;font-family:"Oswald",Arial,sans-serif;font-weight:600;font-size:20px;line-height:33px;white-space:nowrap}
  .reverse-note{left:33px;top:766px;width:245px;text-align:center;font-size:11px;font-style:italic;font-weight:600;color:#333}
  .brand--back{right:28px;top:736px}
</style>
</head>
<body>

<section class="flyer flyer--front" aria-label="Flyer front, promotional offers">
  <svg class="layer" width="570" height="798" viewBox="0 0 570 798">
    <defs>
      <linearGradient id="truckFade" x1="0" y1="0" x2="0" y2="1">
        <stop offset="0" stop-color="#ffffff"/>
        <stop offset=".25" stop-color="#e4e1dc"/>
        <stop offset="1" stop-color="#b9b3ab"/>
      </linearGradient>
      <radialGradient id="burst" cx=".5" cy=".5" r=".5">
        <stop offset="0" stop-color="#fff3a0"/>
        <stop offset="1" stop-color="#ffc414"/>
      </radialGradient>
    </defs>
    <rect x="0" y="490" width="570" height="308" fill="url(#truckFade)" role="img" aria-label="Photo of movers loading boxes into a truck while a family watches"/>
    <circle cx="661" cy="415" r="296" fill="var(--dark)"/>
    <g transform="translate(405 209)">
      <circle r="76" fill="#fff"/>
      <circle r="70" fill="none" stroke="var(--yellow)" stroke-width="10" stroke-dasharray="6 5"/>
      <circle r="68" fill="url(#burst)"/>
    </g>
  </svg>

  <h2 class="abs heading included-title">Included in price</h2>
  <ul class="abs included-list">
    <li>Protection of your furniture with specialized blankets and plastic wrap.</li>
    <li>Disassembly and reassembly of your furniture.</li>
    <li>Wardrobe boxes for the duration of moving process.</li>
  </ul>

  <div class="abs brand brand--front">
    <span class="brand__dot"></span>
    <span class="brand__name">Steadfast Haulers</span>
  </div>

  <p class="abs badge__text">+20% OFF<br>Boxes and<br>Packing<br>supplies</p>

  <div class="abs price price--two">
    <div class="price__amount">$275</div>
    <div class="price__desc">3 hours of<br>Moving Service<br>with</div>
    <div class="price__crew">2 PRO MOVERS</div>
  </div>
  <div class="abs price price--three">
    <div class="price__amount">$325</div>
    <div class="price__desc">3 hours of<br>Moving Service<br>with</div>
    <div class="price__crew">3 PRO MOVERS</div>
  </div>

  <p class="abs heading save">Save<br>15%-<br>25%<br>on<br>your<br>move</p>

  <div class="abs deal">
    <div class="deal__title">Your special deal</div>
    <div class="deal__note">(Cannot be used with any other promotions or coupons)</div>
  </div>

  <p class="abs heading tollfree">Toll free: (800) 555-0148</p>
  <p class="abs voucher-note">Keep this voucher, it is valid until January 1st, 2020</p>
</section>

<section class="flyer flyer--back" aria-label="Flyer back, services">
  <h1 class="abs heading headline">Moving soon?</h1>
  <p class="abs sub-note">Not moving soon? Keep this flyer for later and/or share it with friends. Promotion is valid until January 1st, 2020)</p>

  <div class="abs panel panel--services"></div>
  <div class="abs panel-divider"></div>
  <div class="abs panel panel--why"></div>

  <svg class="layer" width="570" height="798" viewBox="0 0 570 798">
    <defs>
      <linearGradient id="crewPhoto" x1="0" y1="0" x2="1" y2="1">
        <stop offset="0" stop-color="#e7e3dd"/>
        <stop offset=".5" stop-color="#cdbfae"/>
        <stop offset="1" stop-color="#5f79b8"/>
      </linearGradient>
    </defs>
    <circle cx="87" cy="411" r="294" fill="var(--dark)"/>
    <circle cx="87" cy="411" r="284" fill="url(#crewPhoto)" role="img" aria-label="Photo collage of movers carrying boxes, wrapping furniture and loading a truck"/>
    <circle cx="0" cy="411" r="70" fill="var(--dark)"/>
  </svg>

  <h2 class="abs heading services-title">Moving<br>services</h2>
  <ul class="abs list services-list">
    <li>Residential<svg class="tick" viewBox="0 0 12 12"><circle cx="6" cy="6" r="6" fill="#111"/><path d="M3.3 6.2l1.8 1.8 3.6-3.8" fill="none" stroke="#fff" stroke-width="1.5"/></svg></li>
    <li>Long distance<svg class="tick" viewBox="0 0 12 12"><circle cx="6" cy="6" r="6" fill="#111"/><path d="M3.3 6.2l1.8 1.8 3.6-3.8" fill="none" stroke="#fff" stroke-width="1.5"/></svg></li>
    <li>Commercial<svg class="tick" viewBox="0 0 12 12"><circle cx="6" cy="6" r="6" fill="#111"/><path d="M3.3 6.2l1.8 1.8 3.6-3.8" fill="none" stroke="#fff" stroke-width="1.5"/></svg></li>
    <li>Loading /<br>unloading rental<br>truck/portable<br>storage<svg class="tick" viewBox="0 0 12 12"><circle cx="6" cy="6" r="6" fill="#111"/><path d="M3.3 6.2l1.8 1.8 3.6-3.8" fill="none" stroke="#fff" stroke-width="1.5"/></svg></li>
    <li>Packing service<svg class="tick" viewBox="0 0 12 12"><circle cx="6" cy="6" r="6" fill="#111"/><path d="M3.3 6.2l1.8 1.8 3.6-3.8" fill="none" stroke="#fff" stroke-width="1.5"/></svg></li>
  </ul>

  <h3 class="abs why-title">Why Call Us?</h3>
  <ul class="abs list why-list">
    <li>Customer Service Oriented<svg class="tick" viewBox="0 0 12 12"><circle cx="6" cy="6" r="6" fill="#111"/><path d="M3.3 6.2l1.8 1.8 3.6-3.8" fill="none" stroke="#fff" stroke-width="1.5"/></svg></li>
    <li><span>Years of Great reputation<small>(Lots of 5 Star Reviews)</small></span><svg class="tick" viewBox="0 0 12 12"><circle cx="6" cy="6" r="6" fill="#111"/><path d="M3.3 6.2l1.8 1.8 3.6-3.8" fill="none" stroke="#fff" stroke-width="1.5"/></svg></li>
    <li>Affordable pricing<svg class="tick" viewBox="0 0 12 12"><circle cx="6" cy="6" r="6" fill="#111"/><path d="M3.3 6.2l1.8 1.8 3.6-3.8" fill="none" stroke="#fff" stroke-width="1.5"/></svg></li>
    <li>Professional, efficient,<br>strong movers<svg class="tick" viewBox="0 0 12 12"><circle cx="6" cy="6" r="6" fill="#111"/><path d="M3.3 6.2l1.8 1.8 3.6-3.8" fill="none" stroke="#fff" stroke-width="1.5"/></svg></li>
    <li>We always handle your<br>belongings with care<svg class="tick" viewBox="0 0 12 12"><circle cx="6" cy="6" r="6" fill="#111"/><path d="M3.3 6.2l1.8 1.8 3.6-3.8" fill="none" stroke="#fff" stroke-width="1.5"/></svg></li>
    <li>Clean and equipped trucks<svg class="tick" viewBox="0 0 12 12"><circle cx="6" cy="6" r="6" fill="#111"/><path d="M3.3 6.2l1.8 1.8 3.6-3.8" fill="none" stroke="#fff" stroke-width="1.5"/></svg></li>
    <li>Absolutely NO hidden fees<svg class="tick" viewBox="0 0 12 12"><circle cx="6" cy="6" r="6" fill="#111"/><path d="M3.3 6.2l1.8 1.8 3.6-3.8" fill="none" stroke="#fff" stroke-width="1.5"/></svg></li>
  </ul>

  <div class="abs licensed">LICENSED &amp; FULLY INSURED</div>
  <p class="abs reverse-note">See reverse side for promotional offers</p>

  <div class="abs brand brand--back">
    <span class="brand__dot"></span>
    <span class="brand__name">Steadfast Haulers</span>
  </div>
</section>

</body>
</html>
```